Bookcover: Ways to Turn Into a Bold Pathfinder

I am publishing a super-low-cost innovation book for €4,99 on Quillmere Open Press to help everyone become a great innovator: young ambitious people without college education nor a big budget. Do you want to help me?

Brief:
Design a book cover 1600 x 2560 pixels for QOP.
Main title: Ways to Turn Into a Bold Pathfinder
Sub title: mindset - insights - skills & tools
Author: Joost ter Brakel
Design: captive, and appealing to everyone
Target Group: young ambitious people without college education

For quillmere please format the height/width ratio of 1.6:1

```html
<!DOCTYPE html>
<html lang="en">
<head>
<meta charset="utf-8">
<title>Ways to Turn Into a Bold Pathfinder — Book Cover</title>
<link rel="stylesheet" href="https://fonts.googleapis.com/css2?family=Bebas+Neue&family=Montserrat:wght@600;700&display=swap">
<style>
  :root {
    --backdrop: #9e9d9e;
    --cover: #f5f5f5;
    --ink: #000000;
    --accent-red: #fc163e;
    --accent-blue: #23aed8;
    --band-text: #ffffff;
    --art-warm: #fdf3dc;
    --art-light: #fafbfc;
    --art-cool: #e6f3f8;
    --art-edge: #eceef1;
  }
  html, body {
    margin: 0;
    padding: 0;
    width: 1200px;
    height: 1200px;
    overflow: hidden;
    background: var(--backdrop);
  }
  .book-cover-canvas {
    display: block;
    width: 1200px;
    height: 1200px;
  }
  .cover-sheet { fill: var(--cover); }
  .author-name {
    font-family: "Montserrat", sans-serif;
    font-weight: 700;
    font-size: 28px;
    letter-spacing: 1.5px;
    fill: var(--ink);
  }
  .title-lead {
    font-family: "Bebas Neue", sans-serif;
    font-size: 95px;
    fill: var(--ink);
  }
  .title-key {
    font-family: "Bebas Neue", sans-serif;
    font-size: 290px;
    fill: var(--accent-red);
  }
  .title-tail {
    font-family: "Bebas Neue", sans-serif;
    font-size: 162px;
    fill: var(--accent-blue);
  }
  .subtitle-band { fill: var(--accent-red); }
  .subtitle-text {
    font-family: "Montserrat", sans-serif;
    font-weight: 600;
    font-size: 25px;
    letter-spacing: 1px;
    fill: var(--band-text);
  }
  .art-stop-warm { stop-color: var(--art-warm); }
  .art-stop-light { stop-color: var(--art-light); }
  .art-stop-cool { stop-color: var(--art-cool); }
  .art-stop-edge { stop-color: var(--art-edge); }
</style>
</head>
<body>
<svg class="book-cover-canvas" viewBox="0 0 1200 1200" xmlns="http://www.w3.org/2000/svg">
  <defs>
    <radialGradient id="cover-art-fill" cx="52%" cy="42%" r="70%">
      <stop offset="0" class="art-stop-warm"/>
      <stop offset="0.28" class="art-stop-light"/>
      <stop offset="0.6" class="art-stop-cool"/>
      <stop offset="1" class="art-stop-edge"/>
    </radialGradient>
  </defs>

  <rect class="cover-sheet" x="300" y="120" width="600" height="960"/>

  <text class="author-name" x="600" y="165" text-anchor="middle">JOOST TER BRAKEL</text>

  <text class="title-lead" x="355" y="252" textLength="501" lengthAdjust="spacingAndGlyphs">WAYS TO TURN INTO A</text>
  <text class="title-key" x="345" y="477" textLength="519" lengthAdjust="spacingAndGlyphs">BOLD</text>
  <text class="title-tail" x="345" y="606" textLength="519" lengthAdjust="spacingAndGlyphs">PATHFINDER</text>

  <rect class="subtitle-band" x="322" y="626" width="564" height="41"/>
  <text class="subtitle-text" x="604" y="655" text-anchor="middle" textLength="522" lengthAdjust="spacingAndGlyphs">MINDSET - INSIGHTS - SKILLS &amp; TOOLS</text>

  <rect class="cover-art" x="370" y="677" width="468" height="403" fill="url(#cover-art-fill)"
        role="img" aria-label="Illustration: outline of a head in profile with a light bulb full of colourful gears inside"/>
</svg>
</body>
</html>
```